Managed IT services business card design

We haven't needed a business card since the founding of the business in 2005. All our clients have been coming through word of mouth. And lately more and more existing clients are requesting for our business cards to pass on to their contacts in recommending us.
So we needing a business card design. We use various innovative solutions and methodologies to provide IT services to small businesses in managing their IT systems. Our role is the same as an in-house, full-time IT Manager for our clients, but outsourced. So we take care of all our clients' IT needs, just as an IT Manager would be expected to perform.
We have a holding website, which we're happy to leave for now. If we can use the same logo would be great - www.lumadesk.com.au
Preferred colours are shades of are white, grey and black.
We pride our business with the following traits: proactive, good service, prompt response, trustworthy.
Target Market(s)
Small businesses of any industry
Industry/Entity Type
Business

```html
<!DOCTYPE html>
<html lang="en">
<head>
<meta charset="utf-8">
<title>Lumadesk business card</title>
<link rel="stylesheet" href="https://fonts.googleapis.com/css2?family=Open+Sans:wght@400;600&display=swap">
<style>
  :root {
    --backdrop: #dcdcdc;
    --card-white: #ffffff;
    --card-grey: #5a5e62;
    --ink: #1c1c1c;
    --ink-soft: #444444;
    --band-black: #1a1a1a;
    --rule: #2a2a2a;
  }
  * { margin: 0; padding: 0; box-sizing: border-box; }
  html, body {
    width: 1200px; height: 680px; overflow: hidden;
    background: var(--backdrop);
  }
  .canvas { position: relative; width: 1200px; height: 680px; }

  .card {
    position: absolute; top: 191px;
    width: 520px; height: 297px;
    border-radius: 22px; overflow: hidden;
    box-shadow: 0 6px 18px rgba(0,0,0,0.18);
  }
  .card--front { left: 50px; background: var(--card-white); }
  .card--back { left: 630px; background: var(--card-grey); }

  .brand {
    position: absolute;
    display: flex; align-items: center;
    font-family: "Open Sans", sans-serif;
    font-weight: 400;
    line-height: 1;
  }
  .brand__mark { display: block; flex: none; }
  .card--front .brand { left: 38px; top: 120px; gap: 14px; font-size: 34px; color: var(--ink); }
  .card--front .brand__mark { width: 12px; height: 12px; background: var(--ink); }
  .card--back .brand { left: 70px; top: 122px; gap: 18px; font-size: 46px; color: var(--card-white); }
  .card--back .brand__mark { width: 16px; height: 16px; background: var(--card-white); }

  .divider {
    position: absolute; left: 34px; right: 36px; top: 172px;
    height: 1px; background: var(--rule);
  }

  .person {
    position: absolute; right: 40px; top: 140px; text-align: right;
    font-family: "Open Sans", sans-serif; color: var(--ink);
  }
  .person__name { font-size: 17px; letter-spacing: 0.02em; line-height: 26px; }
  .person__role { font-size: 11px; line-height: 14px; color: var(--ink-soft); margin-top: 8px; }

  .address {
    position: absolute; right: 40px; top: 200px; text-align: right;
    font-family: "Open Sans", sans-serif; font-style: normal;
    font-size: 13px; line-height: 17px; color: var(--ink);
  }

  .contacts {
    position: absolute; left: 40px; top: 190px; list-style: none;
    font-family: "Open Sans", sans-serif; font-size: 15px; line-height: 19px; color: var(--ink);
  }
  .contacts li { display: flex; align-items: center; gap: 8px; }
  .contacts svg { width: 13px; height: 13px; flex: none; }

  .card__bands { position: absolute; left: 0; bottom: 0; width: 520px; height: 70px; }

  .web-tab {
    position: absolute; right: 22px; bottom: 13px;
    font-family: "Open Sans", sans-serif; font-size: 13px; letter-spacing: 0.12em;
    white-space: nowrap;
  }
  .card--front .web-tab { color: var(--card-white); }
  .card--back .web-tab { color: var(--ink); }
</style>
</head>
<body>
<main class="canvas">

  <section class="card card--front" aria-label="Business card front">
    <div class="brand"><span>lumadesk</span><span class="brand__mark" aria-hidden="true"></span></div>
    <div class="divider"></div>

    <div class="person">
      <div class="person__name">Mark Ellison</div>
      <div class="person__role">director</div>
    </div>

    <address class="address">
      1480 Kell Ridge Rd<br>Marlow TX 78100
    </address>

    <ul class="contacts">
      <li>
        <svg viewBox="0 0 14 14" aria-label="Phone"><path d="M3 1.5 5.2 4 4 5.6c.8 1.8 2.4 3.4 4.4 4.4L10 8.8l2.5 2.2-1.6 1.8C6 12.6 1.4 8 1.2 3.1z" fill="none" stroke="#333" stroke-width="1.2"/></svg>
        <span>512 004 2750</span>
      </li>
      <li>
        <svg viewBox="0 0 14 14" aria-label="Fax"><rect x="3.5" y="1.5" width="7" height="4" fill="none" stroke="#333" stroke-width="1.1"/><rect x="1.5" y="5.5" width="11" height="7" rx="1" fill="#333"/><rect x="4" y="8" width="6" height="1.2" fill="#fff"/></svg>
        <span>512 004 2751</span>
      </li>
      <li>
        <svg viewBox="0 0 14 14" aria-label="Email"><rect x="1.5" y="3" width="11" height="8" fill="none" stroke="#333" stroke-width="1.2"/><path d="M1.5 3 7 7.5 12.5 3" fill="none" stroke="#333" stroke-width="1.2"/></svg>
        <span>info@lumadesk.com</span>
      </li>
    </ul>

    <svg class="card__bands" viewBox="0 0 520 70" aria-hidden="true">
      <path d="M0 60 L270 38 Q288 36 300 36 L300 70 L0 70 Z" fill="var(--band-black)"/>
      <path d="M302 70 L302 56 Q302 24 334 24 L520 24 L520 70 Z" fill="var(--card-white)"/>
      <path d="M308 70 L308 58 Q308 30 336 30 L520 30 L520 70 Z" fill="var(--card-grey)"/>
    </svg>
    <div class="web-tab">www.lumadesk.com</div>
  </section>

  <section class="card card--back" aria-label="Business card back">
    <div class="brand"><span>lumadesk</span><span class="brand__mark" aria-hidden="true"></span></div>
    <svg class="card__bands" viewBox="0 0 520 70" aria-hidden="true">
      <path d="M300 70 L300 62 Q300 30 332 30 L520 30 L520 70 Z" fill="var(--card-white)"/>
    </svg>
    <div class="web-tab">www.lumadesk.com</div>
  </section>

</main>
</body>
</html>
```